Blogcraft Design Project

NOTICE TO DESIGNERS
****************NOTE: PLEASE DO NOT SUBMIT ANY MORE DESIGNS, THANK YOU!!!!****************
The name of our business is Handset Review Guild and we are setting up a website to review new phones/tablets in the marketplace.
We require a 5 page design, the idea behind the project can be understood better if you visit this websites
1) ravoluna.com
2) http://plvx.com/reviews/cellphones/
Pages required are;
1) Home page which lists all the current top devices
2) A single device page that shows the device with its current specs
3) Comparison page - where 2 or 3 devices are being compared in terms of specs
4) Archive page that shows all the current videos and text reviews
5) Single post page for the device being reviewed with all its pictures, written review, video with sidebar on the side showing other reviews available.
I am opened to a nice color scheme, including red, blue and orange. We do not have any logo at the moment. Thanks
Updates
This is a notice to all designers, I have found the designer I want to work with please do not submit any more designs for now. Thank you
Industry/Entity Type
Business
Look and feel
Each slider illustrates characteristics of the customer's brand and the style your logo design should communicate.

```html
<!DOCTYPE html>
<html lang="en">
<head>
<meta charset="utf-8">
<title>Handset Review Guild – Device Review</title>
<link href="https://fonts.googleapis.com/css2?family=Fjalla+One&family=Open+Sans:wght@300;400;600;700&display=swap" rel="stylesheet">
<style>
:root{
  --red:#ef4d4c;
  --red-deep:#d91f1f;
  --teal:#1f6b6e;
  --teal-dark:#24585a;
  --ink:#444;
  --muted:#666;
  --rule:#d6d6d6;
  --panel:#ececec;
  --panel-edge:#c9c9c9;
  --star-off:#9a9a9a;
  --btn-dark:#333;
  --white:#fff;
}
*{box-sizing:border-box;margin:0;padding:0}
html,body{width:1200px;height:2192px;overflow:hidden;background:var(--white)}
body{position:relative;font-family:"Open Sans",Arial,sans-serif;color:var(--ink)}

/* header */
.site-header{position:absolute;left:0;top:0;width:1200px;height:89px;background:var(--red);border-bottom:4px solid var(--teal-dark)}
.brand{position:absolute;left:183px;top:18px;font-family:"Fjalla One",Arial,sans-serif;font-size:38px;line-height:48px;color:var(--white);text-transform:uppercase}
.main-nav{position:absolute;left:645px;top:47px;display:flex;height:38px}
.main-nav a{display:block;height:38px;padding:9px 16px 0;font-size:14px;font-weight:700;line-height:20px;color:var(--white);text-decoration:none;text-transform:uppercase}
.main-nav a.is-active{background:var(--teal);border-radius:4px 4px 0 0}

/* page title */
.page-title{position:absolute;left:181px;top:98px;font-size:35px;font-weight:300;line-height:46px;color:var(--red)}
.page-title span{color:var(--teal)}
.title-rule{position:absolute;left:175px;top:147px;width:841px;height:2px;background:#e6e6e6}

/* reviews */
.review{position:absolute;left:175px;width:614px;border-bottom:1px dashed var(--rule)}
.review-media{position:absolute;left:0;top:0;width:240px}
.rating-badge{position:absolute;left:3px;top:10px;width:66px;height:66px;border-radius:50%;background:var(--red-deep);border:3px solid var(--white);box-shadow:0 0 0 1px #ddd;color:var(--white);text-align:center;z-index:2}
.rating-badge small{display:block;font-size:14px;line-height:14px;margin-top:12px}
.rating-badge b{display:block;font-size:24px;line-height:26px;font-weight:600}
.device-shot{position:absolute;left:62px;top:8px;width:180px;height:270px;border-radius:22px;background:linear-gradient(160deg,#f2f2f2 0%,#9aa0a8 45%,#1e2227 100%)}
.stars{position:absolute;left:95px;font-size:16px;letter-spacing:1px;color:var(--red)}
.stars .off{color:var(--star-off)}
.actions{position:absolute;left:90px;display:flex;gap:5px}
.btn{display:inline-block;font-size:12px;line-height:17px;padding:0 5px;color:var(--white);border-radius:2px;white-space:nowrap}
.btn-have{background:var(--red)}
.btn-want{background:var(--teal)}
.btn-want.dark{background:var(--btn-dark)}

.review-body{position:absolute;left:271px;top:0;width:345px}
.review-title{font-size:29px;font-weight:300;line-height:31px;color:var(--red);text-transform:uppercase;margin-bottom:10px}
.review-body p{font-size:12px;line-height:20.5px;color:var(--muted)}
.review-body h3{font-size:12px;font-weight:700;color:#333;margin-top:20px;line-height:20px}
.share{display:flex;align-items:center;gap:4px;font-size:12px;color:var(--muted);margin-top:14px}
.share i{display:inline-block;width:17px;height:17px;border-radius:3px}

/* sidebar */
.sidebar{position:absolute;left:808px;top:180px;width:209px;height:1533px;background:var(--panel);border:2px solid var(--panel-edge);border-radius:6px;padding:8px 6px 0}
.sidebar-title{font-size:24px;font-weight:300;color:var(--teal);text-transform:uppercase;line-height:30px;letter-spacing:-.5px;white-space:nowrap}
.side-list{list-style:none;margin-top:2px}
.side-item{display:flex;gap:8px;height:82.6px;padding-top:7px;border-bottom:1px dashed #c4c4c4}
.side-thumb{width:52px;height:58px;flex:none;border:1px solid #d0d0d0;border-radius:4px;background:var(--white);position:relative}
.side-thumb::after{content:"";position:absolute;left:17px;top:8px;width:18px;height:40px;border-radius:4px;background:linear-gradient(#3a3f45,#15181b)}
.side-text{font-size:12px;line-height:16px;color:#444}
.side-text .maker{color:var(--red)}
.side-text .cta{display:block;color:var(--teal);font-weight:700;margin-top:4px}
.side-text .cta::after{content:" ›";color:var(--red)}

/* similar */
.similar{position:absolute;left:183px;top:1739px;width:833px;height:322px;border:2px solid #d0d0d0;border-radius:14px;box-shadow:0 10px 10px -8px rgba(0,0,0,.15)}
.similar-title{text-align:center;font-size:32px;font-weight:300;line-height:40px;margin-top:16px;color:var(--teal);text-transform:uppercase}
.similar-title span{color:var(--red)}
.similar-row{position:absolute;left:30px;top:68px;display:flex}
.similar-item{width:129px;text-align:center;position:relative}
.similar-item .mini-badge{position:absolute;left:18px;top:0;width:40px;height:40px;border-radius:50%;background:var(--red-deep);border:2px solid var(--white);color:var(--white);font-size:18px;font-weight:600;line-height:36px;z-index:2}
.similar-item .mini-shot{display:block;margin:8px auto 0;width:62px;height:145px;border-radius:10px;background:linear-gradient(160deg,#cfd3d8,#2a2e33 55%,#111)}
.similar-item .name{font-size:11.5px;margin-top:12px;color:#333;white-space:nowrap}
.similar-item .name .maker{color:var(--red)}
.similar-item .mini-stars{font-size:12px;letter-spacing:1px;color:var(--red);line-height:14px}
.similar-item .mini-stars .off{color:var(--star-off)}
.similar-item .actions{position:static;justify-content:center;margin-top:10px}
.arrow{position:absolute;top:140px;width:26px;height:26px;border-radius:50%;background:var(--red-deep);border:2px solid var(--white);box-shadow:0 0 0 1px #ccc}
.arrow svg{display:block}
.arrow.prev{left:-14px}
.arrow.next{right:-14px}

/* footer */
.site-footer{position:absolute;left:0;top:2105px;width:1200px;height:87px;background:var(--red);border-top:4px solid var(--teal-dark)}
.footer-nav{position:absolute;left:181px;top:20px;font-size:14px;color:var(--white)}
.footer-nav a{color:var(--white);text-decoration:none}
.footer-nav .sep{margin:0 8px}
.copyright{position:absolute;left:181px;top:43px;font-size:12px;color:var(--white)}
.social{position:absolute;left:926px;top:18px;display:flex;gap:4px}
.social i{display:block;width:28px;height:28px;border-radius:50%;background:var(--white)}
</style>
</head>
<body>

<header class="site-header">
  <div class="brand">Handset Review Guild</div>
  <nav class="main-nav">
    <a href="#">Home</a>
    <a href="#" class="is-active">Reviews</a>
    <a href="#">Tech News</a>
    <a href="#">Contact</a>
  </nav>
</header>

<h1 class="page-title">Device <span>Review</span></h1>
<div class="title-rule"></div>

<article class="review" style="top:180px;height:500px">
  <div class="review-media">
    <div class="rating-badge"><small>Rating</small><b>95</b></div>
    <div class="device-shot" role="img" aria-label="Product photo of the Pomel Pomphone Arc in white and black"></div>
  </div>
  <div class="stars" style="top:302px">★★★★<span class="off">★</span></div>
  <div class="actions" style="top:336px"><span class="btn btn-have">Have it</span><span class="btn btn-want">Want it</span></div>
  <div class="review-body">
    <h2 class="review-title">Vivamus varius arcu eu sagittis aliquam</h2>
    <p>Nullam eget massa vel mi posuere venenatis sed quis tortor. In hac habitasse platea dictumst. Fusce nisi tellus, fermentum a luctus eget, convallis vitae orci. In commodo egestas magna quis placerat. Quisque adipiscing consequat nisi, nec accumsan quam venenatis ac</p>
    <h3>Camera</h3>
    <p>Cras accumsan orci mauris, ut aliquam ipsum faucibus sed. Fusce quam dui, accumsan a magna in, faucibus tristique lectus. Vestibulum sapien leo</p>
    <h3>Call Quality</h3>
    <p>Mauris feugiat aliquam vulputate. Etiam sed mi quis velit commodo mollis et eu quam.</p>
    <h3>Speed and Performance</h3>
    <p>Cras accumsan orci mauris, ut aliquam ipsum faucibus sed. Fusce quam dui, accumsan a magna in, faucibus tristique lectus. Vestibulum sapien leo, placerat quis luctus eget</p>
    <div class="share">Share Review <i style="background:#3b5998"></i><i style="background:#1da1f2"></i><i style="background:#dd4b39"></i></div>
  </div>
</article>

<article class="review" style="top:680px;height:514px">
  <div class="review-media">
    <div class="rating-badge" style="top:13px"><small>Rating</small><b>94</b></div>
    <div class="device-shot" style="left:78px;width:140px;height:272px;top:22px" role="img" aria-label="Product photo of the Kestra Vela Q with its home screen"></div>
  </div>
  <div class="stars" style="top:316px">★★★★<span class="off">★</span></div>
  <div class="actions" style="top:350px"><span class="btn btn-have">Have it</span><span class="btn btn-want">Want it</span></div>
  <div class="review-body" style="top:14px">
    <h2 class="review-title" style="margin-bottom:4px">Maecenas orci est, euismod facilisis feugiat</h2>
    <p>Fusce nisi tellus, fermentum a luctus eget, convallis vitae orci. In commodo egestas magna quis placerat. Quisque adipiscing consequat nisi, nec accumsan quam venenatis ac</p>
    <h3>Camera</h3>
    <p>Cras accumsan orci mauris, ut aliquam ipsum faucibus sed. Fusce quam dui, accumsan a magna in, faucibus tristique lectus. Vestibulum sapien leo</p>
    <h3>Call Quality</h3>
    <p>Mauris feugiat aliquam vulputate. Etiam sed mi quis velit commodo mollis et eu quam.</p>
    <h3>Speed and Performance</h3>
    <p>Cras accumsan orci mauris, ut aliquam ipsum faucibus sed. Fusce quam dui, accumsan a magna in, faucibus tristique lectus. Vestibulum sapien leo, placerat quis luctus eget</p>
    <div class="share">Share Review <i style="background:#3b5998"></i><i style="background:#1da1f2"></i><i style="background:#dd4b39"></i></div>
  </div>
</article>

<article class="review" style="top:1194px;height:519px">
  <div class="review-media">
    <div class="rating-badge" style="top:20px"><small>Rating</small><b>92</b></div>
    <div class="device-shot" style="left:75px;width:144px;height:274px;top:22px;background:linear-gradient(160deg,#f4f4f4 0%,#6fa6d8 35%,#1d4f86 80%,#d9d9d9 100%)" role="img" aria-label="Product photo of the Sorell Orbit Prime with a blue lock screen"></div>
  </div>
  <div class="stars" style="top:321px">★★★★<span class="off">★</span></div>
  <div class="actions" style="top:356px"><span class="btn btn-have">Have it</span><span class="btn btn-want">Want it</span></div>
  <div class="review-body" style="top:18px">
    <h2 class="review-title" style="margin-bottom:4px">Vivamus eu magna rhoncus consectur metus ac</h2>
    <p>Nullam eget massa vel mi posuere venenatis sed quis tortor. In hac habitasse platea dictumst. Fusce nisi tellus, fermentum a luctus eget, convallis vitae orci</p>
    <h3>Camera</h3>
    <p>Cras accumsan orci mauris, ut aliquam ipsum faucibus sed. Fusce quam dui, accumsan a magna in, faucibus tristique lectus. Vestibulum sapien leo</p>
    <h3>Call Quality</h3>
    <p>Mauris feugiat aliquam vulputate. Etiam sed mi quis velit commodo mollis et eu quam.</p>
    <h3>Speed and Performance</h3>
    <p>Cras accumsan orci mauris, ut aliquam ipsum faucibus sed. Fusce quam dui, accumsan a magna in, faucibus tristique lectus. Vestibulum sapien leo, placerat quis luctus eget</p>
    <div class="share">Share Review <i style="background:#3b5998"></i><i style="background:#1da1f2"></i><i style="background:#dd4b39"></i></div>
  </div>
</article>

<aside class="sidebar">
  <h2 class="sidebar-title">Other Reviews</h2>
  <ul class="side-list">
    <li class="side-item"><div class="side-thumb" role="img" aria-label="Kestra Vela Q thumbnail"></div><div class="side-text"><span class="maker">Kestra</span> Vela Q<a class="cta">Check the Review</a></div></li>
    <li class="side-item"><div class="side-thumb" role="img" aria-label="Pomel Pomphone Lite thumbnail"></div><div class="side-text"><span class="maker">Pomel</span> Pomphone Lite<a class="cta">Check the Review</a></div></li>
    <li class="side-item"><div class="side-thumb" role="img" aria-label="Sorell Orbit Nova thumbnail"></div><div class="side-text"><span class="maker">Sorell</span> Orbit<br>Nova<a class="cta">Check the Review</a></div></li>
    <li class="side-item"><div class="side-thumb" role="img" aria-label="Norvik Lumo 610 thumbnail"></div><div class="side-text"><span class="maker">Norvik</span> Lumo 610<a class="cta">Check the Review</a></div></li>
    <li class="side-item"><div class="side-thumb" role="img" aria-label="Kestra Vela Q thumbnail"></div><div class="side-text"><span class="maker">Kestra</span> Vela Q<a class="cta">Check the Review</a></div></li>
    <li class="side-item"><div class="side-thumb" role="img" aria-label="Pomel Pomphone Lite thumbnail"></div><div class="side-text"><span class="maker">Pomel</span> Pomphone Lite<a class="cta">Check the Review</a></div></li>
    <li class="side-item"><div class="side-thumb" role="img" aria-label="Sorell Orbit Nova thumbnail"></div><div class="side-text"><span class="maker">Sorell</span> Orbit<br>Nova<a class="cta">Check the Review</a></div></li>
    <li class="side-item"><div class="side-thumb" role="img" aria-label="Norvik Lumo 610 thumbnail"></div><div class="side-text"><span class="maker">Norvik</span> Lumo 610<a class="cta">Check the Review</a></div></li>
    <li class="side-item"><div class="side-thumb" role="img" aria-label="Kestra Vela Q thumbnail"></div><div class="side-text"><span class="maker">Kestra</span> Vela Q<a class="cta">Check the Review</a></div></li>
    <li class="side-item"><div class="side-thumb" role="img" aria-label="Pomel Pomphone Lite thumbnail"></div><div class="side-text"><span class="maker">Pomel</span> Pomphone Lite<a class="cta">Check the Review</a></div></li>
    <li class="side-item"><div class="side-thumb" role="img" aria-label="Sorell Orbit Nova thumbnail"></div><div class="side-text"><span class="maker">Sorell</span> Orbit<br>Nova<a class="cta">Check the Review</a></div></li>
    <li class="side-item"><div class="side-thumb" role="img" aria-label="Norvik Lumo 610 thumbnail"></div><div class="side-text"><span class="maker">Norvik</span> Lumo 610<a class="cta">Check the Review</a></div></li>
    <li class="side-item"><div class="side-thumb" role="img" aria-label="Kestra Vela Q thumbnail"></div><div class="side-text"><span class="maker">Kestra</span> Vela Q<a class="cta">Check the Review</a></div></li>
    <li class="side-item"><div class="side-thumb" role="img" aria-label="Pomel Pomphone Lite thumbnail"></div><div class="side-text"><span class="maker">Pomel</span> Pomphone Lite<a class="cta">Check the Review</a></div></li>
    <li class="side-item"><div class="side-thumb" role="img" aria-label="Sorell Orbit Nova thumbnail"></div><div class="side-text"><span class="maker">Sorell</span> Orbit<br>Nova<a class="cta">Check the Review</a></div></li>
    <li class="side-item"><div class="side-thumb" role="img" aria-label="Norvik Lumo 610 thumbnail"></div><div class="side-text"><span class="maker">Norvik</span> Lumo 610<a class="cta">Check the Review</a></div></li>
  </ul>
</aside>

<section class="similar">
  <h2 class="similar-title">Similar <span>Smartphones</span></h2>
  <span class="arrow prev"><svg width="22" height="22" viewBox="0 0 22 22"><path d="M13 6l-5 5 5 5" fill="none" stroke="#fff" stroke-width="2.4"/></svg></span>
  <span class="arrow next"><svg width="22" height="22" viewBox="0 0 22 22"><path d="M9 6l5 5-5 5" fill="none" stroke="#fff" stroke-width="2.4"/></svg></span>
  <div class="similar-row">
    <div class="similar-item"><span class="mini-badge">95</span><span class="mini-shot" role="img" aria-label="Pomel Pomphone Arc photo"></span><div class="name"><span class="maker">Pomel</span> Pomphone Arc</div><div class="mini-stars">★★★★★</div><div class="actions"><span class="btn btn-have">Have it</span><span class="btn btn-want dark">Want it</span></div></div>
    <div class="similar-item"><span class="mini-badge">95</span><span class="mini-shot" role="img" aria-label="Kestra Vela Q Plus photo"></span><div class="name"><span class="maker">Kestra</span> Vela Q Plus</div><div class="mini-stars">★★★★<span class="off">★</span></div><div class="actions"><span class="btn btn-have">Have it</span><span class="btn btn-want dark">Want it</span></div></div>
    <div class="similar-item"><span class="mini-badge">94</span><span class="mini-shot" role="img" aria-label="Sorell Orbit R8 photo"></span><div class="name"><span class="maker">Sorell</span> Orbit R8</div><div class="mini-stars">★★★★<span class="off">★</span></div><div class="actions"><span class="btn btn-have">Have it</span><span class="btn btn-want dark">Want it</span></div></div>
    <div class="similar-item"><span class="mini-badge">93</span><span class="mini-shot" role="img" aria-label="Sorell Orbit Duo 3 photo"></span><div class="name"><span class="maker">Sorell</span> Orbit Duo 3</div><div class="mini-stars">★★★★<span class="off">★</span></div><div class="actions"><span class="btn btn-have">Have it</span><span class="btn btn-want dark">Want it</span></div></div>
    <div class="similar-item"><span class="mini-badge">92</span><span class="mini-shot" role="img" aria-label="Norvik Lumo 740 Pro photo"></span><div class="name"><span class="maker">Norvik</span> Lumo 740 Pro</div><div class="mini-stars">★★★★<span class="off">★</span></div><div class="actions"><span class="btn btn-have">Have it</span><span class="btn btn-want dark">Want it</span></div></div>
    <div class="similar-item"><span class="mini-badge">91</span><span class="mini-shot" role="img" aria-label="Pomel Pomphone Lite photo"></span><div class="name"><span class="maker">Pomel</span> Pomphone Lite</div><div class="mini-stars">★★★<span class="off">★★</span></div><div class="actions"><span class="btn btn-have">Have it</span><span class="btn btn-want dark">Want it</span></div></div>
  </div>
</section>

<footer class="site-footer">
  <nav class="footer-nav"><a href="#">Home</a><span class="sep">|</span><a href="#">Reviews</a><span class="sep">|</span><a href="#">Tech News</a><span class="sep">|</span><a href="#">Contact</a></nav>
  <div class="copyright">© Handset Review Guild. All rights reserved</div>
  <div class="social"><i></i><i></i><i></i></div>
</footer>

</body>
</html>
```